Life Coaching business needs a new flyer

We are an Australian business that specialises in Life Coaching, Career Coaching, Health and Wellness Coaching, Yoga and Pilates. We need a A4 double sided flyer that is full colour and folded to DL format. I have attached a couple of designs that I like and some pictures and would like the flyer to be bright yet stylish.

Industry/Entity Type

Life Coaching

```html
<!DOCTYPE html>
<html lang="en">
<head>
<meta charset="utf-8">
<title>Brightpath Coaching – DL Brochure</title>
<link rel="stylesheet" href="https://fonts.googleapis.com/css2?family=Open+Sans:ital,wght@0,400;0,600;0,700;1,400&display=swap">
<style>
:root{
  --blue:#1f6fb5;
  --blue-dark:#184f86;
  --sky:#9fd3ef;
  --green:#7cb83a;
  --green-dark:#5c9a25;
  --ink:#4a4f55;
  --paper:#ffffff;
  --page:#f2f2f2;
}
*{box-sizing:border-box;margin:0;padding:0}
html,body{width:878px;height:1200px;overflow:hidden;background:var(--page);font-family:"Open Sans",Arial,sans-serif;color:var(--ink)}
.sheet{position:absolute;left:0;width:878px;height:585px;background:var(--paper);overflow:hidden}
.sheet--outside{top:0}
.sheet--inside{top:615px}
.panel{position:absolute;top:0;width:292.6px;height:100%;padding:18px 20px}
.panel:nth-child(1){left:0}
.panel:nth-child(2){left:292.6px}
.panel:nth-child(3){left:585.2px}
.swoosh{position:absolute;left:0;bottom:0;width:878px;height:70px}
h2{color:var(--blue);font-size:15px;font-weight:700;margin-bottom:6px}
h3{color:var(--blue);font-size:12px;font-weight:700;margin:8px 0 3px}
p{font-size:7.4px;line-height:1.45;margin-bottom:6px}
.quote{font-style:italic}
.photo{position:absolute;border-radius:2px}
.brand{display:flex;flex-direction:column;align-items:center;gap:6px;color:var(--green-dark);font-weight:700;font-size:15px;text-transform:uppercase;letter-spacing:1px}
.brand-dot{width:44px;height:44px;border-radius:50%;background:var(--green)}
.center{text-align:center}
.contact{font-size:8px;text-align:center;line-height:1.6;color:var(--blue-dark)}
.web{font-size:12px;font-weight:700;color:var(--blue);text-align:center}
.questions{list-style:none}
.questions li{font-size:8px;color:var(--blue);font-weight:600;line-height:1.5;padding-left:11px;position:relative}
.questions li::before{content:"";position:absolute;left:0;top:4px;width:6px;height:6px;background:var(--green);border-radius:50%}
.tagline{color:var(--green-dark);font-style:italic;font-weight:600;font-size:13px;margin:8px 0}
.ticks{list-style:none;margin:4px 0 6px}
.ticks li{font-size:7.6px;line-height:1.55;padding-left:12px;position:relative}
.ticks li::before{content:"✓";position:absolute;left:0;color:var(--green);font-weight:700}
.with-thumb{display:flex;gap:8px}
.with-thumb p{flex:1}
.thumb{width:70px;height:60px;flex:none;border-radius:2px}
</style>
</head>
<body>

<section class="sheet sheet--outside">
  <div class="panel">
    <h2>Happy Client Testimonials</h2>
    <p class="quote">"Working with Anna gave me the courage to change careers. She listened, asked the right questions and helped me find a clear plan I could actually follow every week."<br>– Sarah, Melbourne</p>
    <p class="quote">"I came in feeling stuck and tired. After a few sessions my energy was back, my goals were written down and I finally felt in control of my own life again."<br>– James, Geelong</p>
    <p class="quote">"The yoga and meditation classes changed how I handle stress at work. I sleep better, I think more clearly and I feel calm even on busy days."<br>– Priya, Ballarat</p>
    <p class="quote">"I would recommend Mia to anyone looking for honest support and real results. Her warm approach made every session easy."<br>– Tom, Bendigo</p>
    <div class="photo" role="img" aria-label="Photo of a happy group of friends outdoors" style="left:20px;top:385px;width:252px;height:140px;background:linear-gradient(160deg,#cfe6c0,#8fbf8a 55%,#d9c7a8)"></div>
  </div>
  <div class="panel center">
    <div class="brand"><span class="brand-dot"></span>Brightpath Coaching</div>
    <p style="margin-top:12px">Brightpath Coaching and Meditation Centre is a private practice helping you create balance, purpose and wellbeing in every area of your life.</p>
    <p>We offer life, career and wellness coaching alongside yoga, pilates and guided meditation.</p>
    <div class="photo" role="img" aria-label="Photo of the two coaches" style="left:60px;top:235px;width:172px;height:130px;border-radius:50% 50% 8px 8px;background:linear-gradient(180deg,#bcdff3,#d8b89a)"></div>
    <div style="position:absolute;left:20px;right:20px;top:378px">
      <p class="contact"><strong>Anna Reid &amp; Mia Hart</strong><br>Certified Life Coaches</p>
      <p class="contact">☎ 0400 123 456<br>hello@brightpathcoaching.com.au</p>
    </div>
  </div>
  <div class="panel">
    <div class="photo" role="img" aria-label="Photo of a woman on a mountain top with arms raised" style="left:0;top:0;width:292.6px;height:430px;background:linear-gradient(180deg,#7fbde6,#cfe7f5 45%,#9aa7a0 70%,#6e7d6a)"></div>
    <div style="position:absolute;left:20px;right:20px;top:440px">
      <p class="contact" style="color:var(--green-dark)">Life Coaching · Meditation · Yoga/Pilates</p>
      <p class="web">www.brightpathcoaching.com.au</p>
    </div>
  </div>
  <svg class="swoosh" viewBox="0 0 878 70" preserveAspectRatio="none" aria-hidden="true">
    <path d="M0 40 C220 10 440 70 878 25 L878 70 L0 70Z" fill="var(--sky)"/>
    <path d="M0 52 C250 25 500 75 878 42 L878 70 L0 70Z" fill="var(--green)"/>
    <path d="M0 62 C260 45 520 78 878 58 L878 70 L0 70Z" fill="var(--blue)"/>
  </svg>
</section>

<section class="sheet sheet--inside">
  <div class="panel">
    <ul class="questions">
      <li>Are you looking at making changes this year?</li>
      <li>Are you stuck in a rut or at a crossroads in your life?</li>
      <li>Are you wanting to lose weight but can't get motivated?</li>
      <li>Do you have ongoing problems with your career, relationships or life?</li>
    </ul>
    <p class="tagline">Life coaching is Wonderful!</p>
    <div class="photo" role="img" aria-label="Photo of a sailboat on the open sea" style="left:20px;top:150px;width:252px;height:170px;background:linear-gradient(180deg,#a9d7f2,#3f8fc7 60%,#1f5f95)"></div>
    <div style="position:absolute;left:20px;right:20px;top:335px">
      <h3>Brightpath Coaching and Meditation Centre</h3>
      <p>Our mission is to help you become the best possible person you can be, mentally, physically and spiritually. We offer a warm, supportive space and tailored programs for every client.</p>
      <p>Every program begins with a free chat so we can learn about your goals and build a plan that suits you.</p>
    </div>
  </div>
  <div class="panel">
    <h3 style="margin-top:0">Life Coaching</h3>
    <div class="with-thumb"><p>Life coaching gives you the confidence and clarity to move forward. Together we set goals, remove obstacles and create a clear action plan so you can enjoy a more fulfilling life at home and at work, with support every step.</p><div class="thumb" role="img" aria-label="Photo of a smiling woman" style="background:linear-gradient(160deg,#f3d9c2,#b9d7ea)"></div></div>
    <h3>Career Coaching</h3>
    <div class="with-thumb"><p>Are you at a crossroads in your career or unsure which path to take next? We help you identify strengths, explore options, prepare for interviews and take practical steps toward work you truly enjoy.</p><div class="thumb" role="img" aria-label="Photo of a professional at work" style="background:linear-gradient(160deg,#d6dde6,#8da6bf)"></div></div>
    <h3>Wellness Coaching</h3>
    <div class="with-thumb"><p>Health and wellness coaching helps you build lasting habits around food, movement, sleep and stress. We work with you to create simple routines that fit your lifestyle and keep you motivated.</p><div class="thumb" role="img" aria-label="Photo of fresh healthy food" style="background:linear-gradient(160deg,#d5ecb8,#8cc260)"></div></div>
  </div>
  <div class="panel">
    <h3 style="margin-top:0">Why Would I Need Help?</h3>
    <p>Coaching is for anyone who wants to make lasting changes in their life. Coaching can assist with such issues as:</p>
    <ul class="ticks">
      <li>Finding a better career direction</li>
      <li>Improving relationships</li>
      <li>Weight loss and healthy eating</li>
      <li>Building confidence and self-esteem</li>
      <li>Managing stress and anxiety</li>
      <li>Achieving personal goals and life balance</li>
    </ul>
    <div class="photo" role="img" aria-label="Illustration of figures in yoga poses" style="left:20px;top:200px;width:252px;height:120px;background:linear-gradient(180deg,#eaf6ff,#c9e6f6)"></div>
    <div style="position:absolute;left:20px;right:20px;top:330px">
      <h3>Meditation</h3>
      <p>Our guided meditation sessions help you quiet the mind, reduce stress and find inner calm. Suitable for beginners and experienced students alike.</p>
      <h3>Yoga/Pilates</h3>
      <p>Small group yoga and pilates classes build strength, flexibility and posture in a relaxed, friendly setting. All levels welcome.</p>
    </div>
  </div>
  <svg class="swoosh" viewBox="0 0 878 70" preserveAspectRatio="none" aria-hidden="true">
    <path d="M0 40 C220 10 440 70 878 25 L878 70 L0 70Z" fill="var(--sky)"/>
    <path d="M0 52 C250 25 500 75 878 42 L878 70 L0 70Z" fill="var(--green)"/>
    <path d="M0 62 C260 45 520 78 878 58 L878 70 L0 70Z" fill="var(--blue)"/>
  </svg>
</section>

</body>
</html>
```